KBT Business Cards

We require business cards for our business. We would like a matte black back to the card, with our logo centred in the middle. The front side of the card is open to design.

Target Market(s)

Clients looking for legal services (professional)

Industry/Entity Type

Legal

Contact Information for Business Card

Doran Kelbrath
Partner
Mobile: 0461 738 524
Email: doran@kbtlaw.co
Website: www.kbtlaw.co
Level 3, 118 Wendmore Street
Sydney NSW 2000

Font styles to use
Other font styles liked:
• Avenir

Colors
f04a50
ffffff
1b1b1b

Requirements
Must have
• Black back with logo included in the centre of the card.
• Our font is Avenir.

```html
<!DOCTYPE html>
<html lang="en">
<head>
<meta charset="utf-8">
<title>KBT Business Cards</title>
<link rel="stylesheet" href="https://fonts.googleapis.com/css2?family=Mulish:wght@400;600&display=swap">
<style>
  :root {
    --accent: #f04a50;
    --accent-deep: #c81e45;
    --white: #ffffff;
    --card: #1b1b1b;
    --backdrop: #2a2a2a;
    --emboss: #3a3a3a;
  }
  * { margin: 0; padding: 0; box-sizing: border-box; }
  html, body { width: 1200px; height: 900px; overflow: hidden; }
  body {
    background: var(--backdrop);
    font-family: "Mulish", "Avenir", sans-serif;
    position: relative;
  }
  .card {
    position: absolute;
    left: 320px;
    width: 560px;
    height: 320px;
    background: var(--card);
    border-radius: 14px;
    overflow: hidden;
  }
  .card--back { top: 100px; }
  .card--front { top: 480px; }

  /* back */
  .brand {
    position: absolute;
    left: 0; right: 0; top: 140px;
    display: flex;
    justify-content: center;
    align-items: center;
    gap: 14px;
  }
  .brand__square {
    width: 16px; height: 16px;
    background: var(--emboss);
    flex: none;
  }
  .brand__name {
    color: var(--emboss);
    font-weight: 400;
    font-size: 22px;
    line-height: 28px;
    white-space: nowrap;
  }
  .back-url {
    position: absolute;
    left: 0; right: 0; top: 246px;
    text-align: center;
    color: var(--accent);
    font-size: 13px;
    letter-spacing: 1.5px;
  }

  /* front */
  .edge {
    position: absolute;
    left: 0; right: 0; bottom: 0;
    height: 8px;
    background: var(--accent-deep);
  }
  .identity {
    position: absolute;
    right: 300px; top: 112px;
    text-align: right;
  }
  .identity__name {
    color: var(--accent-deep);
    font-weight: 600;
    font-size: 24px;
    line-height: 30px;
    white-space: nowrap;
  }
  .identity__role {
    color: var(--white);
    font-size: 15px;
    line-height: 20px;
  }
  .divider {
    position: absolute;
    left: 276px; top: 100px;
    width: 1px; height: 76px;
    background: var(--accent-deep);
  }
  .contacts {
    position: absolute;
    left: 296px; top: 98px;
    list-style: none;
  }
  .contacts li {
    display: flex;
    align-items: center;
    gap: 10px;
    color: var(--white);
    font-size: 14px;
    letter-spacing: 0.6px;
    line-height: 26px;
    white-space: nowrap;
  }
  .contacts svg { width: 12px; height: 12px; flex: none; }
  .address {
    position: absolute;
    left: 0; right: 0; top: 250px;
    text-align: center;
    color: var(--white);
    font-size: 14px;
    letter-spacing: 0.4px;
    white-space: nowrap;
  }
</style>
</head>
<body>
  <section class="card card--back">
    <div class="brand">
      <div class="brand__square"></div>
      <p class="brand__name">Kelbrath Brannock Tully Legal</p>
    </div>
    <p class="back-url">www.kbtlaw.co</p>
  </section>

  <section class="card card--front">
    <div class="identity">
      <p class="identity__name">Doran Kelbrath</p>
      <p class="identity__role">Partner</p>
    </div>
    <div class="divider"></div>
    <ul class="contacts">
      <li>
        <svg viewBox="0 0 12 12" aria-hidden="true"><path fill="var(--accent-deep)" d="M2.5 0.8l1.8 2.2-1 1.2c.7 1.5 1.9 2.7 3.4 3.4l1.2-1 2.2 1.8-.9 1.8C6.4 10.4 1.6 5.6 1.8 1.7z"/></svg>
        0461 738 524
      </li>
      <li>
        <svg viewBox="0 0 12 12" aria-hidden="true"><rect x="0.5" y="2" width="11" height="8" fill="var(--accent-deep)"/><path d="M0.8 2.3L6 6.5l5.2-4.2" fill="none" stroke="var(--card)" stroke-width="1"/></svg>
        doran@kbtlaw.co
      </li>
      <li>
        <svg viewBox="0 0 12 12" aria-hidden="true"><circle cx="6" cy="6" r="5.5" fill="var(--accent-deep)"/><path d="M0.5 6h11M6 0.5c-2.4 3-2.4 8 0 11M6 0.5c2.4 3 2.4 8 0 11" fill="none" stroke="var(--card)" stroke-width="0.8"/></svg>
        www.kbtlaw.co
      </li>
    </ul>
    <p class="address">Level 3, 118 Wendmore Street Sydney NSW 2000</p>
    <div class="edge"></div>
  </section>
</body>
</html>
```